I have a logo and need to design the business card and stationery.
Updates

The uploaded logo image named as GREYMARSH CONSTRUCTION which is to be replaced to GREYMARSH CONTRACTS. Kindly add below details and submit the designs- Company name- Greymarsh Engineering Contracts LLP Name & Post- Kelvan Joshi (Designated Partner) Address- Block No.317, Wing C, Tulvo Trade Court, Manek Pural Road, Ruparel Industrial Estate, Goregaon(E), Mumbai - 400 063 Contact- +91 97415 60382 Email- kelvanjoshi@mailbrook.example Website- www.greymarshcontracts.example Contact for Letterhead- +91-22-28754193

Hi Tovin Rahul, We are liking your Design #28860835. We have suggested some changes which are mentioned in feedback. Kindly revert with it asap to finalize this design.

Colors

Designer to choose colors to be used in the design.

```html
<!DOCTYPE html>
<html lang="en">
<head>
<meta charset="utf-8">
<title>Greymarsh Contracts Stationery</title>
<link href="https://fonts.googleapis.com/css2?family=Open+Sans:wght@400;600&display=swap" rel="stylesheet">
<style>
  :root {
    --backdrop: #dcdcdc;
    --paper: #f4f4f4;
    --ink: #0a0a0a;
    --body-text: #555555;
    --header-text: #ffffff;
    --muted-light: #bdbdbd;
    --signature-tone: #d2d2d2;
  }
  * { box-sizing: border-box; margin: 0; padding: 0; }
  html, body { width: 1200px; height: 884px; overflow: hidden; }
  body {
    background: var(--backdrop);
    font-family: "Open Sans", sans-serif;
    position: relative;
  }

  /* Letterhead */
  .letterhead {
    position: absolute;
    left: 40px;
    top: 22px;
    width: 594px;
    height: 840px;
    background: var(--paper);
    box-shadow: 0 6px 18px rgba(0,0,0,0.18);
  }
  .letterhead-header {
    height: 128px;
    background: var(--ink);
    display: flex;
    justify-content: space-between;
    align-items: center;
    padding: 0 32px 0 40px;
    color: var(--header-text);
  }
  .brand { display: flex; align-items: center; gap: 12px; }
  .brand-square {
    width: 30px;
    height: 30px;
    border: 3px solid var(--header-text);
    flex: none;
  }
  .brand-name {
    font-weight: 600;
    font-size: 15px;
    letter-spacing: 1px;
    line-height: 1.25;
  }
  .brand-sub {
    display: block;
    letter-spacing: 4.4px;
    font-size: 10px;
  }
  .contact-list {
    list-style: none;
    font-size: 8.5px;
    line-height: 1.5;
    width: 250px;
  }
  .contact-list li { display: flex; align-items: flex-start; gap: 6px; }
  .contact-list svg { width: 9px; height: 9px; fill: var(--header-text); flex: none; margin-top: 2px; }
  .letter-body {
    padding: 58px 52px 0 60px;
    color: var(--body-text);
    font-size: 10.6px;
    line-height: 1.52;
  }
  .salutation { margin-bottom: 10px; }
  .paragraph { text-indent: 24px; margin-bottom: 10px; }
  .closing { margin-top: 12px; }
  .signature {
    margin-top: 12px;
    width: 90px;
    height: 44px;
    background: var(--signature-tone);
    border-radius: 4px;
  }

  /* Business card */
  .business-card {
    position: absolute;
    left: 678px;
    width: 482px;
    height: 276px;
    background: var(--ink);
    color: var(--header-text);
    box-shadow: 0 6px 18px rgba(0,0,0,0.22);
  }
  .card-front {
    top: 140px;
    display: flex;
    align-items: center;
    justify-content: center;
  }
  .card-front .brand-square { width: 44px; height: 44px; border-width: 4px; }
  .card-front .brand-name { font-size: 24px; letter-spacing: 2px; }
  .card-front .brand-sub { font-size: 14px; letter-spacing: 8px; }
  .card-front .brand { gap: 16px; }
  .card-back {
    top: 468px;
    padding: 30px 34px;
    display: flex;
    flex-direction: column;
    justify-content: space-between;
  }
  .holder-name { font-size: 18px; font-weight: 600; letter-spacing: 1px; }
  .holder-role { font-size: 11px; color: var(--muted-light); margin-top: 2px; }
  .company-line { font-size: 11px; font-weight: 600; margin-top: 8px; }
  .card-contacts { list-style: none; font-size: 10px; line-height: 1.6; }
  .card-contacts li { display: flex; align-items: flex-start; gap: 8px; }
  .card-contacts svg { width: 10px; height: 10px; fill: var(--header-text); flex: none; margin-top: 3px; }
</style>
</head>
<body>
  <article class="letterhead">
    <header class="letterhead-header">
      <div class="brand">
        <span class="brand-square"></span>
        <span class="brand-name">GREYMARSH<span class="brand-sub">CONTRACTS</span></span>
      </div>
      <ul class="contact-list">
        <li>
          <svg viewBox="0 0 10 10" aria-hidden="true"><path d="M5 0.5 A3.4 3.4 0 0 1 8.4 3.9 C8.4 6.2 5 9.5 5 9.5 C5 9.5 1.6 6.2 1.6 3.9 A3.4 3.4 0 0 1 5 0.5 Z M5 2.6 A1.3 1.3 0 1 0 5 5.2 A1.3 1.3 0 1 0 5 2.6 Z" fill-rule="evenodd"/></svg>
          <span>Block No.317, Wing C, Tulvo Trade Court, Manek Pural Road, Ruparel Industrial Estate, Goregaon(E), Mumbai - 400 063</span>
        </li>
        <li>
          <svg viewBox="0 0 10 10" aria-hidden="true"><path d="M2 0.5 L3.8 2.6 L2.9 3.8 Q4 6 6.2 7.1 L7.4 6.2 L9.5 8 L8.4 9.5 Q3.5 9 0.5 1.6 Z"/></svg>
          <span>+91-22-28754193</span>
        </li>
        <li>
          <svg viewBox="0 0 10 10" aria-hidden="true"><path d="M0.5 2 H9.5 V8 H0.5 Z M1.2 2.6 L5 5.4 L8.8 2.6 Z" fill-rule="evenodd"/></svg>
          <span>kelvanjoshi@mailbrook.example</span>
        </li>
        <li>
          <svg viewBox="0 0 10 10" aria-hidden="true"><circle cx="5" cy="5" r="4.5"/></svg>
          <span>www.greymarshcontracts.example</span>
        </li>
      </ul>
    </header>
    <section class="letter-body">
      <p class="salutation">Dear customer,</p>
      <p class="paragraph">Lorem ipsum dolor sit amet, consectetur adipisicing elit, sed do eiusmod tempor incididunt ut labore et dolore magna aliqua. Ut enim ad minim veniam, quis nostrud exercitation ullamco laboris nisi ut aliquip ex ea commodo consequat. Duis aute irure dolor in reprehenderit in voluptate velit esse cillum dolore eu fugiat nulla pariatur. Excepteur sint occaecat cupidatat non proident, sunt in culpa qui officia deserunt mollit anim id est laborum.</p>
      <p class="paragraph">Lorem ipsum dolor sit amet, consectetur adipisicing elit, sed do eiusmod tempor incididunt ut labore et dolore magna aliqua. Ut enim ad minim veniam, quis nostrud exercitation ullamco laboris nisi ut aliquip ex ea commodo consequat. Duis aute irure dolor in reprehenderit in voluptate velit esse cillum dolore eu fugiat nulla pariatur. Excepteur sint occaecat cupidatat non proident, sunt in culpa qui officia deserunt mollit anim id est laborum.</p>
      <p class="paragraph">Lorem ipsum dolor sit amet, consectetur adipisicing elit, sed do eiusmod tempor incididunt ut labore et dolore magna aliqua. Ut enim ad minim veniam, quis nostrud exercitation ullamco laboris nisi ut aliquip ex ea commodo consequat. Duis aute irure dolor in reprehenderit in voluptate velit esse cillum dolore eu fugiat nulla pariatur. Excepteur sint occaecat cupidatat non proident, sunt in culpa qui officia deserunt mollit anim id est laborum.</p>
      <p class="paragraph">Lorem ipsum dolor sit amet, consectetur adipisicing elit, sed do eiusmod tempor incididunt ut labore et dolore magna aliqua. Ut enim ad minim veniam, quis nostrud exercitation ullamco laboris nisi ut aliquip ex ea commodo consequat. Duis aute irure dolor in reprehenderit.</p>
      <p class="closing">Yours Sincerely,</p>
      <div class="signature" role="img" aria-label="Handwritten signature of the sender"></div>
    </section>
  </article>

  <section class="business-card card-front">
    <div class="brand">
      <span class="brand-square"></span>
      <span class="brand-name">GREYMARSH<span class="brand-sub">CONTRACTS</span></span>
    </div>
  </section>

  <section class="business-card card-back">
    <div class="card-holder">
      <p class="holder-name">Kelvan Joshi</p>
      <p class="holder-role">Designated Partner</p>
      <p class="company-line">Greymarsh Engineering Contracts LLP</p>
    </div>
    <ul class="card-contacts">
      <li>
        <svg viewBox="0 0 10 10" aria-hidden="true"><path d="M2 0.5 L3.8 2.6 L2.9 3.8 Q4 6 6.2 7.1 L7.4 6.2 L9.5 8 L8.4 9.5 Q3.5 9 0.5 1.6 Z"/></svg>
        <span>+91 97415 60382</span>
      </li>
      <li>
        <svg viewBox="0 0 10 10" aria-hidden="true"><path d="M0.5 2 H9.5 V8 H0.5 Z M1.2 2.6 L5 5.4 L8.8 2.6 Z" fill-rule="evenodd"/></svg>
        <span>kelvanjoshi@mailbrook.example</span>
      </li>
      <li>
        <svg viewBox="0 0 10 10" aria-hidden="true"><circle cx="5" cy="5" r="4.5"/></svg>
        <span>www.greymarshcontracts.example</span>
      </li>
      <li>
        <svg viewBox="0 0 10 10" aria-hidden="true"><path d="M5 0.5 A3.4 3.4 0 0 1 8.4 3.9 C8.4 6.2 5 9.5 5 9.5 C5 9.5 1.6 6.2 1.6 3.9 A3.4 3.4 0 0 1 5 0.5 Z M5 2.6 A1.3 1.3 0 1 0 5 5.2 A1.3 1.3 0 1 0 5 2.6 Z" fill-rule="evenodd"/></svg>
        <span>Block No.317, Wing C, Tulvo Trade Court, Manek Pural Road, Ruparel Industrial Estate, Goregaon(E), Mumbai - 400 063</span>
      </li>
    </ul>
  </section>
</body>
</html>
```